Black Car Limousine transportation business in Naples Florida

Always stand for my reliability and RVD stands for Love, K and M are the first initials of my children's names. It should show professionalism and a dedication to customer service. We keep our clients identities private. Show our professionalism. We are Black car Black tie company. We service transportation on a reserve basis to and from residents, airports, casinos, hotels,

Target Market(s)

It is a Private car service. High end clients. Businesses, Celebrity and athletes. Service to airports, hotels, special events.

Industry/Entity Type

Business

Contact Information for Business Card

A pearl metallic or Luster card. Standard business card size. Would like the name, Company email, show we take credit cards and phone number. Currently I don't have a website but will like to add later.

Logo Text

STEADFAST RVD TRANSPORTATION

Font styles to use
Serif

Colors
eaeaea
000000

Requirements
Must have
• Must have Company email, show we take credit cards and phone number. Currently I don't have a website but will like to add later.
Nice to have
• Would like to stay with a black and white theme. Open to some color trim.
Should not have
• Open to suggestions

```html
<!DOCTYPE html>
<html lang="en">
<head>
<meta charset="utf-8">
<title>STEADFAST RVD TRANSPORTATION – Business Card</title>
<link rel="stylesheet" href="https://fonts.googleapis.com/css2?family=Source+Serif+4:opsz,wght@8..60,400;8..60,600;8..60,700&display=swap">
<style>
  :root {
    --backdrop: #6f6f6f;
    --card-light: #ffffff;
    --ink: #2a2a2a;
    --ink-soft: #4a4a4a;
    --card-dark: #1b1b1b;
    --paper-white: #ffffff;
  }
  * { margin: 0; padding: 0; box-sizing: border-box; }
  html, body {
    width: 1200px; height: 900px; overflow: hidden;
    background: var(--backdrop);
    font-family: "Source Serif 4", Georgia, serif;
  }
  .canvas { position: relative; width: 1200px; height: 900px; }

  .card {
    position: absolute; top: 306px;
    width: 440px; height: 271px;
    border-radius: 10px; overflow: hidden;
  }
  .card--front { left: 149px; background: var(--card-light); }
  .card--back { left: 608px; background: var(--card-dark); }

  .brand {
    position: absolute;
    font-weight: 700; color: var(--ink);
    line-height: 1;
  }
  .brand__top { display: block; font-size: 12px; letter-spacing: 3px; }
  .brand__main { display: block; font-size: 64px; letter-spacing: 1px; margin-top: 0; }
  .brand__bottom { display: block; font-size: 19px; letter-spacing: 0.6px; margin-top: 0; }

  .card--front .brand { left: 28px; top: 86px; }
  .card--back .brand { left: 60px; top: 160px; color: var(--paper-white); }
  .card--back .brand__top { font-size: 9px; letter-spacing: 2.4px; }
  .card--back .brand__main { font-size: 48px; }
  .card--back .brand__bottom { font-size: 14.5px; letter-spacing: 0.5px; }

  .contact { position: absolute; left: 251px; top: 60px; color: var(--ink-soft); font-size: 12.5px; line-height: 16px; }
  .contact__name { font-size: 15.5px; font-weight: 600; color: var(--ink); line-height: 19px; }
  .contact__role { margin-bottom: 10px; }
  .contact__address { margin-bottom: 10px; }
  .contact__list { list-style: none; }
  .contact__list li { display: flex; align-items: center; gap: 7px; }
  .contact__list svg { width: 10px; height: 10px; fill: var(--ink); flex: none; }

  .vehicle-photo {
    position: absolute; inset: 0;
    background:
      radial-gradient(ellipse 40% 60% at 70% 55%, #2e2e2e 0%, #1a1a1a 60%, #141414 100%),
      linear-gradient(#111 0%, #1e1e1e 40%, #2a2a2a 100%);
  }
</style>
</head>
<body>
<main class="canvas">
  <section class="card card--front" aria-label="Card front">
    <div class="brand">
      <span class="brand__top">STEADFAST</span>
      <span class="brand__main">RVD</span>
      <span class="brand__bottom">TRANSPORTATION</span>
    </div>
    <div class="contact">
      <p class="contact__name">Marcus Hale</p>
      <p class="contact__role">Managing Director</p>
      <p class="contact__address">4100 Harbor Lane, Suite 8<br>Naples, FL 34102.</p>
      <ul class="contact__list">
        <li><svg viewBox="0 0 10 10" aria-hidden="true"><path d="M2 0.5 L3.6 0.5 L4.2 2.8 L3.1 3.7 Q4 5.8 6.3 6.9 L7.2 5.8 L9.5 6.4 L9.5 8 Q9.5 9.5 8 9.5 Q0.5 9 0.5 2 Q0.5 0.5 2 0.5 Z"/></svg>044-555 010 246</li>
        <li><svg viewBox="0 0 10 10" aria-hidden="true"><path d="M0.5 2 H9.5 V8 H0.5 Z M0.5 2 L5 5.4 L9.5 2" /></svg>info@rvdcars.com</li>
        <li><svg viewBox="0 0 10 10" aria-hidden="true"><path d="M0.5 2 H9.5 V8 H0.5 Z"/><rect x="0.5" y="3.4" width="9" height="1.2" fill="#ffffff"/></svg>All major credit cards</li>
      </ul>
    </div>
  </section>

  <section class="card card--back" aria-label="Card back">
    <div class="vehicle-photo" role="img" aria-label="Photograph of a black luxury SUV, front view, on a dark paved lot"></div>
    <div class="brand">
      <span class="brand__top">STEADFAST</span>
      <span class="brand__main">RVD</span>
      <span class="brand__bottom">TRANSPORTATION</span>
    </div>
  </section>
</main>
</body>
</html>
```